Casino with the 'highest winning percentage' needs a stationery design

This is for a casino in Colombo, Sri Lanka and we need a stationery design for business card, letter head and envelope.

Should be very professional, simple and elegant without fancy fonts

Reason: Not fully satisfied with the designs. Need more designs.

Business

• 1. card deck symbol 'CLUBS' in red, or black

2. name in BLOCK CAPITAL LETTERS

3. Preferred font colours are black, white or red

4. Prefer 'professional /elegant' fonts
• SHOULD NOT HAVE ANY OTHER SYMBOL EXCEPT 'CLUBS'

DO NOT PREFER ITALIC FONTS

```html
<!DOCTYPE html>
<html lang="en">
<head>
<meta charset="utf-8">
<title>Marlow's Entertainment – Business Card</title>
<link href="https://fonts.googleapis.com/css2?family=Noto+Serif:wght@400;700&display=swap" rel="stylesheet">
<style>
  :root {
    --backdrop: #e9e6e2;
    --card: #ffffff;
    --card-edge: #9a948e;
    --brand-red: #d62a3e;
    --ink: #111111;
    --body-ink: #222222;
    --faint-mark: #fbecec;
  }
  * { margin: 0; padding: 0; box-sizing: border-box; }
  html, body {
    width: 1200px;
    height: 372px;
    overflow: hidden;
    background: var(--backdrop);
    font-family: "Noto Serif", Georgia, serif;
  }
  .canvas {
    position: relative;
    width: 1200px;
    height: 372px;
  }
  .card {
    position: absolute;
    top: 28px;
    width: 555px;
    height: 316px;
    background: var(--card);
    border: 1px solid var(--card-edge);
    overflow: hidden;
  }
  .card--front { left: 33px; }
  .card--back { left: 622px; }

  .brand-dot {
    position: absolute;
    border-radius: 50%;
    background: var(--brand-red);
  }
  .brand-name {
    position: absolute;
    color: var(--ink);
    font-weight: 700;
    letter-spacing: 0.02em;
    white-space: nowrap;
  }
  .card--front .brand-dot { left: 42px; top: 22px; width: 84px; height: 84px; }
  .card--front .brand-name { left: 149px; top: 26px; font-size: 27px; line-height: 37px; }
  .card--back .brand-dot { left: 66px; top: 100px; width: 102px; height: 102px; }
  .card--back .brand-name { left: 194px; top: 104px; font-size: 32px; line-height: 44px; }

  .faint-mark {
    position: absolute;
    left: 396px;
    top: 130px;
    width: 118px;
    height: 118px;
    border-radius: 50%;
    background: var(--faint-mark);
  }

  .company-label {
    position: absolute;
    left: 38px;
    top: 129px;
    font-size: 12.5px;
    line-height: 18px;
    font-weight: 700;
    color: var(--brand-red);
    padding-bottom: 1px;
    border-bottom: 1.5px solid var(--brand-red);
    letter-spacing: 0.02em;
  }
  .address {
    position: absolute;
    left: 38px;
    top: 152px;
    font-size: 12.5px;
    line-height: 19px;
    color: var(--body-ink);
    font-style: normal;
  }
  .contact-list {
    position: absolute;
    left: 38px;
    top: 203px;
    list-style: none;
    font-size: 12.5px;
    line-height: 20.5px;
    color: var(--body-ink);
  }
  .contact-key { color: var(--brand-red); font-weight: 700; }
  .web-accent { color: var(--brand-red); font-weight: 700; }

  .tagline {
    position: absolute;
    left: 0;
    right: 0;
    top: 261px;
    text-align: center;
    font-size: 15px;
    line-height: 20px;
    font-weight: 700;
    letter-spacing: 0.14em;
    color: var(--brand-red);
  }
</style>
</head>
<body>
<main class="canvas">
  <section class="card card--front" aria-label="Business card front">
    <span class="brand-dot" aria-hidden="true"></span>
    <h1 class="brand-name">MARLOW'S<br>ENTERTAINMENT</h1>
    <span class="faint-mark" aria-hidden="true"></span>
    <p class="company-label">MARLOW'S LIMITED</p>
    <address class="address">58, Lotus Gate Mawatha<br>Colombo 01000, Sri Lanka</address>
    <ul class="contact-list">
      <li><span class="contact-key">P :</span> + 94 11 2456780</li>
      <li><span class="contact-key">C :</span> + 94 77 0000000</li>
      <li><span class="contact-key">F :</span> + 94 11 0000000</li>
      <li><span class="contact-key">E :</span> info@marlowscolombo.com</li>
      <li>www.<span class="web-accent">marlowscolombo</span>.com</li>
    </ul>
  </section>

  <section class="card card--back" aria-label="Business card back">
    <span class="brand-dot" aria-hidden="true"></span>
    <h2 class="brand-name">MARLOW'S<br>ENTERTAINMENT</h2>
    <p class="tagline">HIGHEST WINNING PERCENTAGE IN THE WORLD</p>
  </section>
</main>
</body>
</html>
```